Business card for Sports Apparel business

DOUBLE SIDED DESIGN
We need business cards for a new sports apparel business. We are developing a protective headband for soccer initially.
Torvalle is focused on designing and developing head protection products to reduce the likelihood of concussion when playing sports. Exploring and understanding medical insights, material science research, current and former players experiences and governing bodies guidelines has allowed Torvalle to develop the safety, style, form and function requirements of a suitable product to bring to market.
Target Market(s)
Mums buying kits for the sons and daughters. Amateur footballers.
Industry/Entity Type
Sporting Good
Contact Information for Business Card
Martin Ashworth - CEO
Mobile: +44 7431589027
Email: martin@torvalle.co.uk
Tel: 0208 5519372
Helena Pargeter - COO
Mob: +44 7385 640117
Email: helena@torvalle.co.uk
Tel: 0208 5519372
Duncan Farrow - CCO
Mob: +44 7564 293081
Email: duncan@torvalle.co.uk
Tel: 0208 5519372
Look and feel
Each slider illustrates characteristics of the customer's brand and the style your logo design should communicate.

```html
<!DOCTYPE html>
<html lang="en">
<head>
<meta charset="utf-8">
<title>Torvalle — Business Card</title>
<link href="https://fonts.googleapis.com/css2?family=Montserrat:wght@400;500;600;700&display=swap" rel="stylesheet">
<style>
  :root {
    --stage: #1b1b1c;
    --card: #2a2a2b;
    --card-edge: #232324;
    --brand-blue: #1a6fb3;
    --silver: #cfcfd1;
    --white: #f2f2f2;
    --muted: #d8d8d8;
  }
  * { margin: 0; padding: 0; box-sizing: border-box; }
  html, body {
    width: 1200px; height: 900px; overflow: hidden;
    background: var(--stage);
    font-family: "Montserrat", sans-serif;
  }
  .sheet {
    position: relative; width: 1200px; height: 900px;
    display: flex; flex-direction: column; align-items: center;
    justify-content: center; gap: 34px;
  }
  .card {
    position: relative; width: 700px; height: 400px;
    background: radial-gradient(ellipse at 75% 60%, #333334 0%, var(--card) 45%, var(--card-edge) 100%);
    box-shadow: 0 18px 40px rgba(0,0,0,0.55);
    overflow: hidden;
  }
  .card__band {
    position: absolute; left: 0; right: 0; bottom: 0; height: 7px;
    background: var(--brand-blue);
  }
  /* Front */
  .card--front { display: flex; align-items: center; justify-content: center; }
  .wordmark--front {
    font-weight: 600; font-size: 54px; letter-spacing: 6px;
    color: var(--silver); text-transform: uppercase;
  }
  /* Back */
  .card--back { display: flex; align-items: center; }
  .brand-block {
    width: 330px; display: flex; align-items: center; justify-content: center; gap: 12px;
  }
  .brand-block__square { width: 18px; height: 18px; background: var(--brand-blue); }
  .wordmark--back {
    font-weight: 600; font-size: 38px; letter-spacing: 3px;
    color: var(--white); text-transform: uppercase;
  }
  .divider { width: 2px; height: 160px; background: var(--brand-blue); margin-right: 34px; }
  .contact { color: var(--white); }
  .contact__name {
    font-weight: 600; font-size: 21px; letter-spacing: 2px;
    color: var(--brand-blue); text-transform: uppercase;
  }
  .contact__role { font-size: 16px; color: var(--muted); margin: 2px 0 18px; letter-spacing: 1px; }
  .contact__list { list-style: none; }
  .contact__item {
    display: flex; align-items: center; gap: 12px;
    font-size: 17px; letter-spacing: 0.8px; line-height: 28px;
  }
  .contact__icon { width: 15px; height: 15px; flex: none; }
</style>
</head>
<body>
<main class="sheet">
  <section class="card card--front" aria-label="Card front">
    <span class="wordmark--front">Torvalle</span>
    <div class="card__band"></div>
  </section>

  <section class="card card--back" aria-label="Card back">
    <div class="brand-block">
      <span class="brand-block__square"></span>
      <span class="wordmark--back">Torvalle</span>
    </div>
    <div class="divider"></div>
    <div class="contact">
      <h1 class="contact__name">Martin Ashworth</h1>
      <p class="contact__role">CEO</p>
      <ul class="contact__list">
        <li class="contact__item">
          <svg class="contact__icon" viewBox="0 0 16 16"><path d="M4 1 L6.5 4.5 L5 6.5 Q6.5 9.5 9.5 11 L11.5 9.5 L15 12 L13 15 Q5 14 1 3 Z" fill="var(--brand-blue)"/></svg>
          0208 5519372
        </li>
        <li class="contact__item">
          <svg class="contact__icon" viewBox="0 0 16 16"><rect x="4" y="1" width="8" height="14" rx="1.5" fill="none" stroke="var(--brand-blue)" stroke-width="1.5"/><circle cx="8" cy="12.5" r="0.9" fill="var(--brand-blue)"/></svg>
          +44 7431589027
        </li>
        <li class="contact__item">
          <svg class="contact__icon" viewBox="0 0 16 16"><rect x="1" y="3.5" width="14" height="9" fill="none" stroke="var(--brand-blue)" stroke-width="1.4"/><path d="M1 3.5 L8 9 L15 3.5" fill="none" stroke="var(--brand-blue)" stroke-width="1.4"/></svg>
          martin@torvalle.co.uk
        </li>
        <li class="contact__item">
          <svg class="contact__icon" viewBox="0 0 16 16"><circle cx="8" cy="8" r="6.5" fill="none" stroke="var(--brand-blue)" stroke-width="1.3"/><ellipse cx="8" cy="8" rx="2.8" ry="6.5" fill="none" stroke="var(--brand-blue)" stroke-width="1.1"/><path d="M1.5 8 H14.5 M2.5 5 H13.5 M2.5 11 H13.5" stroke="var(--brand-blue)" stroke-width="1"/></svg>
          www.torvalle.co.uk
        </li>
      </ul>
    </div>
    <div class="card__band"></div>
  </section>
</main>
</body>
</html>
```